Corporate profile brochure for a Technology Company

We are a technology corporation with offices in multiple countries across the globe. We are needing to have a new company profile brochure designed. We will provide the content. Additional images can be added by designer where they see fit. We provide technology services and solutions to large multinational customers around the world and we partner with some of the largest companies in the world. The design should have a corporate, professional look and feel with combination of text and visual elements. We would like to see something with the colours Red, Black and White as Red is our default colour as per our logo. Logo can be provided in vector format if requested. Brochure should be in booklet style with multi pages.
Need extra days to review

```html
<!DOCTYPE html>
<html lang="en">
<head>
<meta charset="utf-8">
<title>KESTREL Technology Services – Company Profile</title>
<link rel="stylesheet" href="https://fonts.googleapis.com/css2?family=Anton&family=Archivo:wght@400;600;700&display=swap">
<style>
  :root{
    --stage:#ecebea;
    --page:#262224;
    --page-deep:#1c191a;
    --red:#e0262b;
    --red-deep:#b81d22;
    --white:#ffffff;
    --ink:#161415;
    --grey-box:#d9d9d9;
    --muted:#3a3537;
    --orange:#f39a2b;
    --body:'Archivo', Arial, sans-serif;
    --display:'Anton', Impact, sans-serif;
  }
  *{box-sizing:border-box;margin:0;padding:0}
  html,body{width:1200px;height:906px;overflow:hidden;background:var(--stage);font-family:var(--body)}
  .canvas{position:relative;width:1200px;height:906px}
  .page,.spread{position:absolute;overflow:hidden;background:var(--page);box-shadow:0 4px 12px rgba(0,0,0,.25)}
  .spread .half{position:absolute;top:0;width:50%;height:100%;overflow:hidden}
  .half.left{left:0}
  .half.right{left:50%;background:linear-gradient(160deg,#2b2527 0%,#3a1e21 60%,#231e20 100%)}
  .wordmark{font-family:var(--body);font-weight:700;letter-spacing:.04em;white-space:nowrap}
  .heading{position:absolute;font-family:var(--display);font-size:31px;line-height:1;display:flex;gap:6px;align-items:center}
  .heading .boxed{background:var(--white);color:var(--ink);padding:1px 4px}
  .heading .red{color:var(--red)}
  .copy{position:absolute;color:#e9e6e6;font-size:8.2px;line-height:1.3}
  .photo{position:absolute}

  /* back cover */
  .back-cover{left:63px;top:65px;width:247px;height:350px;background:linear-gradient(135deg,#2c292b,#252224)}
  .back-cover .spine-mark{position:absolute;left:30px;top:330px;transform:rotate(-90deg);transform-origin:left top;color:#1d1a1c;font-size:40px}
  .back-cover .spine-sub{position:absolute;left:70px;top:330px;transform:rotate(-90deg);transform-origin:left top;color:#3b3739;font-size:17px;font-weight:400;letter-spacing:.12em}
  .back-cover .spine-line{position:absolute;right:12px;top:0;width:1px;height:100%;background:#1e1b1d}

  /* front cover */
  .front-cover{left:329px;top:65px;width:247px;height:350px;background:linear-gradient(180deg,#2a2426,#1f1b1d)}
  .front-cover .brand{position:absolute;top:33px;left:0;width:100%;text-align:center;color:var(--white);font-size:20px;line-height:1}
  .front-cover .brand small{display:block;font-size:9.5px;letter-spacing:.2em;margin-top:2px}

  /* about spread */
  .about{left:636px;top:62px;width:494px;height:353px}
  .about .values{position:absolute;left:26px;top:0;width:189px;height:176px;background:var(--grey-box);padding:28px 14px 0 12px;color:var(--ink)}
  .values h4{font-size:8px;font-weight:700;margin-bottom:9px}
  .values ul{list-style:none;display:flex;flex-wrap:wrap;gap:10px 14px;font-size:8px;margin-bottom:12px}
  .values li{display:flex;align-items:center;gap:3px}
  .values li::before{content:"";width:7px;height:7px;border-radius:50%;background:var(--red)}
  .values p{font-size:6.6px;line-height:1.25;margin-bottom:6px}
  .mission{position:absolute;left:34px;color:var(--white);font-size:8.2px;line-height:1.25;width:140px}
  .mission b{font-weight:700;display:block}
  .about .foot-mark{position:absolute;left:34px;top:322px;color:var(--red-deep);font-size:15px}

  /* who we are spread */
  .who{left:74px;top:486px;width:492px;height:350px}
  .who .callout{position:absolute;left:282px;top:57px;width:180px;height:83px;background:var(--red);color:var(--white);font-size:8px;line-height:1.25;padding:11px 10px}
  .faint-mark{position:absolute;color:#1a1718;font-size:15px}

  /* service spread */
  .service{left:640px;top:486px;width:491px;height:350px}
  .service-map{position:absolute;left:0;top:0;width:491px;height:350px}
  .svc-label{position:absolute;color:var(--white);font-size:8px;font-weight:700;white-space:nowrap;transform:translateX(-50%)}
  .hub-mark{position:absolute;left:247px;top:324px;transform:translateX(-50%);color:var(--white);font-size:11px;text-align:center;line-height:1}
  .hub-mark small{display:block;font-size:5.5px;letter-spacing:.15em}
</style>
</head>
<body>
<main class="canvas">

  <!-- Back cover -->
  <section class="page back-cover" aria-label="Back cover">
    <div class="spine-mark wordmark">KESTREL</div>
    <div class="spine-sub wordmark">TECHNOLOGY SERVICES</div>
    <div class="spine-line"></div>
  </section>

  <!-- Front cover -->
  <section class="page front-cover" aria-label="Front cover">
    <div class="brand wordmark">KESTREL<small>TECHNOLOGY SERVICES</small></div>
    <div class="photo" role="img" aria-label="Glowing digital globe with network connections above a light ring"
         style="left:30px;top:135px;width:190px;height:200px;background:radial-gradient(circle at 50% 42%,#3a5f6e 0%,#3a2c35 40%,rgba(31,27,29,0) 70%)"></div>
    <svg style="position:absolute;left:0;top:0" width="247" height="350" aria-hidden="true">
      <polygon points="123,220 170,309 77,309" fill="var(--red)"/>
    </svg>
  </section>

  <!-- About spread -->
  <section class="spread about" aria-label="About spread">
    <div class="half left" style="background:var(--page-deep)">
      <svg style="position:absolute;left:0;top:0" width="247" height="353" aria-hidden="true">
        <polygon points="84,114 248,353 0,353 0,220" fill="var(--red)"/>
      </svg>
      <div class="heading" style="left:34px;top:24px"><span class="boxed">ABOUT</span><span class="red">KTS</span></div>
      <p class="copy" style="left:34px;top:63px;width:182px">At KESTREL Technology Services (KTS), our customers are at the heart of everything we do. KTS provides personalized technology solutions and services to customers across the globe.</p>
      <div class="mission" style="top:196px"><b>Our Mission</b>is to make the world more connected &amp; efficient through engineering, technology, &amp; innovation.</div>
      <div class="mission" style="top:255px;width:130px"><b>Our Vision</b>Vision is to be a global leader in innovation &amp; development of new technological solutions to solve our customers' challenges.</div>
      <div class="foot-mark wordmark">KESTREL</div>
    </div>
    <div class="half right">
      <div class="values">
        <h4>Our Values</h4>
        <ul><li>Trust</li><li>Innovation</li><li>Integrity</li><li>Safety</li><li>Leadership</li></ul>
        <p>For over a decade, KTS has been working with large multinational organizations, providing our customers with bespoke ICT services, enterprise solutions and consultancy.</p>
        <p>Through our philosophy of collaborations and innovations, we believe technology has the potential to revolutionize every aspect of our future.</p>
      </div>
      <div class="photo" role="img" aria-label="Open hand holding a glowing network globe"
           style="left:0;top:176px;width:247px;height:177px;background:radial-gradient(ellipse at 55% 60%,#c98a6a 0%,#7a3a34 25%,#3a2226 55%,rgba(35,30,32,0) 80%)"></div>
    </div>
  </section>

  <!-- Who we are spread -->
  <section class="spread who" aria-label="Who we are spread">
    <div class="half left" style="background:var(--page-deep)"></div>
    <div class="half right" style="background:linear-gradient(180deg,#2b2627,#231f21)"></div>
    <div class="photo" role="img" aria-label="Two hands reaching toward a glowing network globe over a blurred city at night"
         style="left:0;top:117px;width:492px;height:233px;background:linear-gradient(180deg,rgba(35,31,33,0) 0%,#22394a 35%,#1f3444 70%,#172430 100%)"></div>
    <div class="heading" style="left:34px;top:24px"><span class="boxed">WHO</span><span class="red">WE ARE</span></div>
    <p class="copy" style="left:34px;top:66px;width:175px">KTS delivers ICT services and solutions across the Asia Pacific region, leveraging our expertise to optimize efficiency and effectiveness across a wide variety of industry sectors.</p>
    <div class="faint-mark wordmark" style="left:313px;top:26px">KESTREL</div>
    <div class="callout">Our turnkey solutions span from engagement to resolution, complemented by dedicated service desks across multiple time zones to provide round-the-clock support in compliance with ISO &amp; ITIL-4 standards.</div>
  </section>

  <!-- Service spread -->
  <section class="spread service" aria-label="Services spread">
    <div class="half left" style="background:var(--page-deep)"></div>
    <div class="half right"></div>
    <div class="heading" style="left:31px;top:24px"><span class="red">KTS</span><span class="boxed">SERVICE</span></div>
    <p class="copy" style="left:31px;top:66px;width:190px">We support our customers' unique requirements with flexible solutions including Project Workforce, Outsourced Support &amp; Master Service Agreements. KTS' services include IT Service Desks, On-Site / FTE Support, Project Management, Procurement / Hardware Management, Cloud and Enterprise Solutions.</p>
    <div class="faint-mark wordmark" style="left:310px;top:26px">KESTREL</div>

    <svg class="service-map" viewBox="0 0 491 350" aria-hidden="true">
      <g stroke="#7a2a2e" stroke-width="1" fill="none">
        <line x1="74" y1="215" x2="210" y2="300"/>
        <line x1="175" y1="231" x2="225" y2="295"/>
        <line x1="109" y1="293" x2="185" y2="318"/>
        <line x1="259" y1="215" x2="250" y2="282"/>
        <line x1="340" y1="196" x2="275" y2="290"/>
        <line x1="440" y1="189" x2="290" y2="300"/>
        <line x1="392" y1="286" x2="305" y2="320"/>
      </g>
      <circle cx="247" cy="350" r="70" fill="#3a1517" stroke="var(--red-deep)" stroke-width="2"/>
      <circle cx="247" cy="350" r="55" fill="none" stroke="#5a1e22" stroke-width="1"/>
      <g fill="#2a1719" stroke="var(--red)" stroke-width="1.5">
        <circle cx="74" cy="215" r="30"/>
        <circle cx="175" cy="231" r="21"/>
        <circle cx="109" cy="293" r="28"/>
        <circle cx="259" cy="215" r="26"/>
        <circle cx="340" cy="196" r="26"/>
        <circle cx="392" cy="286" r="28"/>
      </g>
      <circle cx="440" cy="189" r="30" fill="#3a1e16" stroke="var(--orange)" stroke-width="2.5"/>
      <g fill="var(--white)">
        <circle cx="74" cy="210" r="8" fill="none" stroke="var(--white)" stroke-width="1.5"/>
        <rect x="68" y="220" width="12" height="6"/>
        <rect x="169" y="225" width="12" height="12" fill="none" stroke="var(--white)" stroke-width="1.5"/>
        <circle cx="109" cy="293" r="8" fill="none" stroke="var(--white)" stroke-width="2"/>
        <ellipse cx="259" cy="213" rx="10" ry="6"/>
        <rect x="333" y="190" width="14" height="3"/><rect x="338" y="193" width="4" height="9"/>
        <circle cx="440" cy="187" r="8" fill="none" stroke="var(--white)" stroke-width="2"/>
        <circle cx="392" cy="282" r="6"/><rect x="384" y="289" width="16" height="6" rx="3"/>
      </g>
    </svg>
    <span class="svc-label" style="left:74px;top:172px">Field FTE</span>
    <span class="svc-label" style="left:175px;top:198px">Infrastructure</span>
    <span class="svc-label" style="left:86px;top:265px">IT Support</span>
    <span class="svc-label" style="left:254px;top:178px">Cloud</span>
    <span class="svc-label" style="left:343px;top:160px">On Site Workforce</span>
    <span class="svc-label" style="left:440px;top:150px">Aviation</span>
    <span class="svc-label" style="left:425px;top:248px">24/7 Service Desk</span>
    <div class="hub-mark wordmark">KESTREL<small>TECHNOLOGY SERVICES</small></div>
  </section>

</main>
</body>
</html>
```